Modern Verdell Tree Care Website

I need a website for a full service Tree Care company. The company provides tree pruning, tree removal, tree preservation, emergency services, stump grinding, and emergency tree services.

Target Market(s)

Customers that need tree services

Industry/Entity Type

Landscaping, Tree Services

Coding

Coded - Design and coding required

Number of Pages Required

5+ page

Font styles to use
Sans Serif

Requirements
Must have
• Good clean design that showcases the services the company provides.
Nice to have
• Services page; contact form, blog, home page, about page

```html
<!DOCTYPE html>
<html lang="en">
<head>
<meta charset="utf-8">
<title>Verdell Tree Care</title>
<link href="https://fonts.googleapis.com/css2?family=Lexend:wght@400;500;600&family=Montserrat:wght@400;500;600;700&display=swap" rel="stylesheet">
<style>
:root{
  --green:#7dc242;
  --green-dark:#4f9a2c;
  --orange:#f8a93a;
  --ink:#2f2f2f;
  --text:#444;
  --beige:#f1f0e8;
  --line:#e3c9a8;
  --white:#fff;
}
*{box-sizing:border-box;margin:0;padding:0}
html,body{width:1200px;height:4376px;overflow:hidden}
body{position:relative;font-family:"Montserrat",sans-serif;color:var(--text);background:var(--white)}
.abs{position:absolute}
.heading{font-family:"Lexend",sans-serif;font-weight:500;letter-spacing:1px;color:var(--ink);text-transform:uppercase}
.heading .accent{color:var(--green)}
.brand{font-family:"Lexend",sans-serif;font-weight:600;color:var(--ink);letter-spacing:1px}
.btn{position:absolute;background:var(--orange);color:var(--white);font-weight:700;font-size:13px;letter-spacing:1px;display:flex;align-items:center;justify-content:center;clip-path:polygon(12% 0,100% 0,88% 100%,0 100%);text-transform:uppercase}

/* header */
.site-header{position:absolute;top:0;left:0;width:1200px;height:83px;background:var(--white)}
.logo{position:absolute;display:flex;align-items:center;gap:12px}
.logo-mark{width:38px;height:38px;border-radius:50%;background:var(--green)}
.logo-text{font-family:"Lexend",sans-serif;font-weight:600;font-size:30px;line-height:1;color:var(--ink);letter-spacing:1px}
.nav{position:absolute;top:30px;left:340px;display:flex;font-size:13px;letter-spacing:1.5px;font-weight:500;color:var(--ink)}
.nav span{padding:0 30px;border-left:1px solid #ccc}
.nav span:first-child{border:none;padding-left:0;color:var(--green);border-bottom:2px solid var(--green);padding-bottom:8px}
.phone-tab{position:absolute;right:0;top:0;width:235px;height:83px;background:var(--green);clip-path:polygon(12% 0,100% 0,100% 100%,0 100%);display:flex;align-items:center;justify-content:flex-end;padding-right:26px;color:var(--white);font-size:15px;letter-spacing:1.5px;gap:10px}

/* hero */
.hero-photo{left:0;top:83px;width:1200px;height:622px;background:linear-gradient(110deg,#c7a58c 0%,#8e6f57 35%,#6c8a3b 60%,#a8c95a 100%)}
.hero-frame{left:306px;top:160px;width:608px;height:153px;border:3px solid var(--green);border-top:none}
.hero-frame::before,.hero-frame::after{content:"";position:absolute;top:0;height:3px;background:var(--green);width:60px}
.hero-frame::before{left:-3px}.hero-frame::after{right:-3px}
.hero-title{left:306px;width:608px;top:140px;text-align:center;font-size:37px;line-height:46px;color:var(--ink)}
.hero-sub{left:306px;width:608px;top:250px;text-align:center;font-size:18px;color:var(--ink)}

/* about */
.about-panel{left:0;top:740px;width:352px;height:565px;background:linear-gradient(160deg,#6fb53a,#4f9a2c)}
.about-ring{left:113px;top:790px;width:466px;height:466px;border-radius:50%;border:3px solid var(--orange);background:var(--white)}
.about-photo{left:130px;top:807px;width:432px;height:432px;border-radius:50%;background:linear-gradient(160deg,#5c9d34,#a8cf6c 60%,#d9e6c4)}
.about-heading{left:606px;top:826px;font-size:36px;line-height:44px}
.about-copy{left:613px;top:932px;width:510px;font-size:15px;line-height:23px;color:var(--text)}
.about-copy p+p{margin-top:23px}

/* services */
.services{left:0;top:1337px;width:1200px;height:808px;background:var(--beige)}
.section-title{position:absolute;left:0;width:1200px;text-align:center;font-size:36px}
.tri{position:absolute;width:0;height:0;border-left:12px solid transparent;border-right:12px solid transparent;border-bottom:24px solid var(--green)}
.svc-img{position:absolute;width:328px;height:207px}
.svc-icon{position:absolute;width:64px;height:64px;border-radius:50%;background:var(--green);border:4px solid var(--white);display:flex;align-items:center;justify-content:center}
.svc-icon.alt{background:var(--orange)}
.svc-label{position:absolute;font-family:"Lexend",sans-serif;font-weight:500;font-size:19px;color:var(--ink);line-height:24px;letter-spacing:.5px}

/* why */
.diamond{position:absolute;width:176px;height:176px;transform:rotate(45deg);border:1.5px solid var(--line);background:var(--white)}
.diamond.on{background:var(--orange);border-color:var(--orange)}
.why-item{position:absolute;width:200px;text-align:center;font-weight:700;font-size:14px;line-height:20px;color:var(--ink)}
.why-item.on{color:var(--white)}

/* blogs */
.blogs{left:0;top:2750px;width:1200px;height:600px;background:linear-gradient(180deg,#eef0ea,#f6f7f2 70%,#fff)}
.card{position:absolute;background:var(--white);border:1px solid #ddd}
.tag{position:absolute;background:var(--green);color:var(--white);font-weight:700;font-size:12px;padding:6px 14px}
.blog-text{position:absolute;font-weight:600;color:var(--ink)}
.more{color:var(--green-dark);font-weight:700;text-decoration:underline;font-size:13px;display:block}

/* contact */
.contact-bg{left:0;top:3335px;width:1200px;height:690px;background:linear-gradient(160deg,#74bd3c,#4f9a2c 70%,#3f8a25)}
.field{position:absolute;background:var(--white);height:57px;display:flex;align-items:center;padding-left:25px;gap:10px;font-size:14px;color:#555}

/* footer */
.foot-col{position:absolute;top:4020px;height:356px;border-left:1px solid #e5e5e5}
.foot-h{position:absolute;font-family:"Lexend",sans-serif;font-size:18px;color:var(--ink)}
.foot-h::before{content:"";position:absolute;left:-18px;top:2px;border-left:5px solid transparent;border-right:5px solid transparent;border-bottom:12px solid var(--orange)}
.foot-list{position:absolute;font-size:13px;line-height:29px;color:var(--ink)}
.social{position:absolute;top:4137px;width:26px;height:26px;border-radius:50%;border:2px solid var(--orange)}
</style>
</head>
<body>

<header class="site-header">
  <div class="logo" style="left:95px;top:16px">
    <div class="logo-mark"></div>
    <div class="logo-text">VERDELL<div style="font-size:15px;font-weight:400;color:var(--green);letter-spacing:4px;margin-top:4px">TREE CARE</div></div>
  </div>
  <nav class="nav"><span>HOME</span><span>ABOUT US</span><span>SERVICES</span><span>BLOG</span><span>CONTACT US</span></nav>
  <div class="phone-tab">
    <svg width="24" height="24" viewBox="0 0 24 24"><circle cx="12" cy="12" r="12" fill="#fff"/><path d="M8 6l2.5 0 1 3-1.5 1c.8 1.8 2 3 4 4l1-1.5 3 1V16c0 1-1 2-2 2C10 18 6 14 6 8c0-1 1-2 2-2z" fill="#7dc242"/></svg>
    (555) 014 2290
  </div>
</header>

<section>
  <div class="abs hero-photo" role="img" aria-label="Close-up of gloved hand pruning a leafy branch with shears"></div>
  <svg class="abs" style="left:0;top:560px" width="1200" height="150" viewBox="0 0 1200 150">
    <polygon points="0,15 700,90 1200,0 1200,150 0,150" fill="#7dc242"/>
    <polygon points="0,15 700,90 640,150 0,150" fill="#f8a93a"/>
    <polygon points="0,140 1200,150 0,150" fill="#fff"/>
  </svg>
  <div class="abs hero-frame"></div>
  <h1 class="abs heading hero-title"><span style="background:transparent;padding:0 12px">VERDELL FOR ALL YOUR<br>TREE CARE NEEDS</span></h1>
  <p class="abs hero-sub">Serving Brookhaven and surrounding areas.</p>
  <div class="btn" style="left:522px;top:292px;width:178px;height:42px">CONTACT US</div>
</section>

<section>
  <div class="abs about-panel" role="img" aria-label="Green tinted photo of foliage"></div>
  <div class="abs about-ring"></div>
  <div class="abs about-photo" role="img" aria-label="Arborist trimming branches with long-handled loppers"></div>
  <h2 class="abs heading about-heading">ABOUT VERDELL<br><span class="accent">TREE CARE</span></h2>
  <div class="tri" style="left:853px;top:872px"></div>
  <svg class="abs" style="left:915px;top:884px" width="285" height="10"><circle cx="5" cy="5" r="4" fill="#f8a93a"/><line x1="14" y1="5" x2="285" y2="5" stroke="#f8a93a" stroke-width="1"/></svg>
  <div class="abs about-copy">
    <p>At Verdell Tree Care, we are more than just a tree service company, we are stewards of our beautiful trees. With a passion deeply rooted in arboriculture, we embark on a mission to promote the health, beauty, and safety of your trees and landscapes.</p>
    <p>Whether it's expert tree trimming to enhance aesthetics, meticulous tree removal to mitigate hazards, or comprehensive tree health assessments to ensure safety , we approach each task with unwavering dedication and attension to detail.</p>
  </div>
  <div class="btn" style="left:590px;top:1172px;width:180px;height:45px">LEARN MORE</div>
</section>

<section>
  <div class="abs services"></div>
  <div class="tri" style="left:588px;top:1388px"></div>
  <h2 class="heading section-title" style="top:1418px">OUR <span class="accent">SERVICES</span></h2>

  <div class="svc-img" style="left:86px;top:1493px;background:linear-gradient(135deg,#8fb45a,#5d7a3a)" role="img" aria-label="Pruning shears cutting a branch"></div>
  <div class="svc-img" style="left:431px;top:1493px;background:linear-gradient(135deg,#6f5a3c,#4c6b2c)" role="img" aria-label="Chainsaw cutting into a tree trunk"></div>
  <div class="svc-img" style="left:779px;top:1493px;background:linear-gradient(135deg,#6d9b3a,#6b4a30)" role="img" aria-label="Shovel digging soil beside a plant"></div>
  <div class="svc-img" style="left:90px;top:1775px;background:linear-gradient(135deg,#9a4b3a,#b38a54)" role="img" aria-label="Stump grinder at work on a tree stump"></div>
  <div class="svc-img" style="left:435px;top:1775px;background:linear-gradient(135deg,#7c9a5a,#5b6a48)" role="img" aria-label="Fallen tree after a storm"></div>
  <div class="svc-img" style="left:783px;top:1775px;background:linear-gradient(135deg,#4a78b8,#7a5a3a)" role="img" aria-label="Climber roped into a tree canopy"></div>

  <div class="svc-icon" style="left:106px;top:1680px"><svg width="30" height="30" viewBox="0 0 30 30" fill="none" stroke="#fff" stroke-width="2"><path d="M6 24L20 10M10 24l14-14M20 10l4-4M24 10l2-2"/></svg></div>
  <div class="svc-icon alt" style="left:451px;top:1680px"><svg width="30" height="30" viewBox="0 0 30 30" fill="none" stroke="#fff" stroke-width="2"><rect x="6" y="14" width="18" height="10"/><path d="M10 14V8h10v6"/></svg></div>
  <div class="svc-icon" style="left:799px;top:1680px"><svg width="30" height="30" viewBox="0 0 30 30" fill="none" stroke="#fff" stroke-width="2"><path d="M15 4l9 4v7c0 6-4 9-9 11-5-2-9-5-9-11V8z"/></svg></div>
  <div class="svc-icon" style="left:110px;top:1962px"><svg width="30" height="30" viewBox="0 0 30 30" fill="none" stroke="#fff" stroke-width="2"><circle cx="15" cy="15" r="9"/><path d="M15 6v18M6 15h18"/></svg></div>
  <div class="svc-icon" style="left:455px;top:1962px"><svg width="30" height="30" viewBox="0 0 30 30" fill="none" stroke="#fff" stroke-width="2"><path d="M15 4c6 0 8 6 6 12H9C7 10 9 4 15 4zM15 16v10"/></svg></div>
  <div class="svc-icon" style="left:803px;top:1962px"><svg width="30" height="30" viewBox="0 0 30 30" fill="none" stroke="#fff" stroke-width="2"><circle cx="15" cy="12" r="7"/><path d="M15 19v7M10 26h10"/></svg></div>

  <div class="svc-label" style="left:184px;top:1707px">TREE PRUNING</div>
  <div class="svc-label" style="left:528px;top:1707px">TREE REMOVAL</div>
  <div class="svc-label" style="left:871px;top:1708px">TREE PRESERVATION</div>
  <div class="svc-label" style="left:187px;top:1996px">STUMP GRINDING</div>
  <div class="svc-label" style="left:531px;top:1990px">TREE EMERGENCY<br>SERVICES</div>
  <div class="svc-label" style="left:877px;top:1991px">CABLING &amp; BRACING</div>
</section>

<section>
  <div class="tri" style="left:598px;top:2180px"></div>
  <h2 class="heading section-title" style="top:2212px">WHY <span class="accent">CHOOSE US</span></h2>

  <div class="diamond" style="left:112px;top:2325px"></div>
  <div class="diamond on" style="left:376px;top:2325px"></div>
  <div class="diamond" style="left:640px;top:2325px"></div>
  <div class="diamond" style="left:906px;top:2325px"></div>
  <div class="diamond" style="left:244px;top:2468px"></div>
  <div class="diamond" style="left:510px;top:2468px"></div>
  <div class="diamond" style="left:777px;top:2468px"></div>

  <svg class="abs" style="left:178px;top:2343px" width="44" height="48" fill="none" stroke="#7dc242" stroke-width="2"><rect x="4" y="6" width="26" height="36"/><circle cx="32" cy="32" r="9"/><path d="M28 32l3 3 5-6"/></svg>
  <svg class="abs" style="left:442px;top:2343px" width="44" height="48" fill="none" stroke="#fff" stroke-width="2"><path d="M22 4c10 0 12 12 6 18H16C10 16 12 4 22 4zM22 22v22M14 44h16"/></svg>
  <svg class="abs" style="left:706px;top:2340px" width="44" height="52" fill="none" stroke="#7dc242" stroke-width="2"><path d="M22 4a13 13 0 0 1 13 13c0 10-13 24-13 24S9 27 9 17A13 13 0 0 1 22 4z"/><circle cx="22" cy="17" r="5"/><ellipse cx="22" cy="46" rx="14" ry="4"/></svg>
  <svg class="abs" style="left:972px;top:2343px" width="44" height="48" fill="none" stroke="#7dc242" stroke-width="2"><rect x="4" y="8" width="24" height="34"/><rect x="18" y="4" width="22" height="30"/><path d="M22 12h14M22 18h14M22 24h10"/></svg>
  <svg class="abs" style="left:306px;top:2484px" width="52" height="52" fill="none" stroke="#7dc242" stroke-width="2"><path d="M40 14A20 20 0 1 0 26 46"/><path d="M26 14v12l6 4"/><text x="28" y="48" font-size="20" fill="none" stroke="#7dc242" stroke-width="1.2" font-family="Montserrat,sans-serif">24</text></svg>
  <svg class="abs" style="left:574px;top:2490px" width="44" height="46" fill="none" stroke="#7dc242" stroke-width="2"><path d="M10 18a12 12 0 0 1 24 0zM6 18h32"/><circle cx="22" cy="26" r="6"/><path d="M8 44c2-8 8-10 14-10s12 2 14 10"/></svg>
  <svg class="abs" style="left:840px;top:2486px" width="50" height="50" fill="none" stroke="#7dc242" stroke-width="2"><circle cx="25" cy="10" r="6"/><circle cx="10" cy="20" r="5"/><circle cx="40" cy="20" r="5"/><path d="M14 40c0-8 5-14 11-14s11 6 11 14M2 38c0-6 3-10 8-10M48 38c0-6-3-10-8-10"/></svg>

  <div class="why-item" style="left:100px;top:2410px">LICENSED AND<br>INSURED</div>
  <div class="why-item on" style="left:364px;top:2410px">PROFESSIONAL<br>WORK</div>
  <div class="why-item" style="left:628px;top:2410px">LOCALLY OWNED<br>&amp; OPERATED</div>
  <div class="why-item" style="left:894px;top:2410px">FREE ESTIMATE</div>
  <div class="why-item" style="left:232px;top:2555px">24 HOUR EMERGENCY<br>SERVICES</div>
  <div class="why-item" style="left:498px;top:2555px">SAFETY IS OUR<br>TOP PRIORITY</div>
  <div class="why-item" style="left:765px;top:2555px">LICENSED ARBORIST<br>ON STAFF</div>
</section>

<section>
  <div class="abs blogs"></div>
  <div class="tri" style="left:584px;top:2780px"></div>
  <h2 class="heading section-title" style="top:2812px;left:-18px">LATEST <span class="accent">BLOGS</span></h2>

  <div class="card" style="left:106px;top:2903px;width:474px;height:405px">
    <div class="abs" style="left:0;top:0;width:472px;height:282px;background:linear-gradient(135deg,#7a7d72,#5b5244 60%,#8a8276)" role="img" aria-label="Worker cutting a large trunk with a chainsaw"></div>
    <div class="tag" style="left:16px;top:256px">20 MAY 2024</div>
    <div class="blog-text" style="left:38px;top:306px;width:400px;font-size:17px;line-height:26px">Lorem ipsum dolor sit amet consectetur adipiscing elit sed do eiusmod<span class="more" style="margin-top:4px">LEARN MORE</span></div>
  </div>

  <div class="card" style="left:600px;top:2903px;width:500px;height:194px">
    <div class="abs" style="left:0;top:0;width:236px;height:192px;background:linear-gradient(135deg,#a8b08a,#5e6a3c)" role="img" aria-label="Arborist climbing a tree trunk"></div>
    <div class="tag" style="left:262px;top:38px;font-size:10px;padding:4px 12px">20 MAY 2024</div>
    <div class="blog-text" style="left:262px;top:74px;width:210px;font-size:13px;line-height:19px">Lorem ipsum dolor sit amet consectetur adipiscing elit sed do eiusmod<span class="more" style="font-size:11px;margin-top:4px">LEARN MORE</span></div>
  </div>

  <div class="card" style="left:600px;top:3115px;width:500px;height:194px">
    <div class="abs" style="left:0;top:0;width:236px;height:192px;background:linear-gradient(160deg,#5c9d34,#a8cf6c 60%,#d9e6c4)" role="img" aria-label="Arborist trimming branches with loppers"></div>
    <div class="tag" style="left:266px;top:32px;font-size:10px;padding:4px 12px">10 MAY 2024</div>
    <div class="blog-text" style="left:266px;top:70px;width:210px;font-size:13px;line-height:19px">Lorem ipsum dolor sit amet consectetur adipiscing elit sed do eiusmod<span class="more" style="font-size:11px;margin-top:4px">LEARN MORE</span></div>
  </div>
</section>

<section>
  <div class="abs contact-bg" role="img" aria-label="Green tinted foliage background"></div>
  <svg class="abs" style="left:0;top:3335px" width="1200" height="140" viewBox="0 0 1200 140">
    <polygon points="0,0 1200,70 1200,0" fill="#f6f7f2"/>
    <polygon points="0,0 650,55 1200,0 1200,70 0,140" fill="#7dc242" opacity=".8"/>
    <polygon points="0,0 650,55 0,140" fill="#f8a93a"/>
  </svg>
  <div class="tri" style="left:591px;top:3470px;border-bottom-color:#fff"></div>
  <h2 class="heading section-title" style="top:3512px;color:#fff">CONTACT US</h2>

  <div class="field" style="left:222px;top:3592px;width:376px"><svg width="14" height="14" fill="#888"><circle cx="7" cy="4" r="3.5"/><path d="M0 14c0-5 3-7 7-7s7 2 7 7z"/></svg>First Name*</div>
  <div class="field" style="left:613px;top:3592px;width:377px"><svg width="14" height="14" fill="#888"><circle cx="7" cy="4" r="3.5"/><path d="M0 14c0-5 3-7 7-7s7 2 7 7z"/></svg>Last Name*</div>
  <div class="field" style="left:222px;top:3660px;width:376px"><svg width="14" height="12" fill="none" stroke="#888" stroke-width="1.5"><rect x="1" y="1" width="12" height="10"/><path d="M1 1l6 5 6-5"/></svg>Email address</div>
  <div class="field" style="left:613px;top:3660px;width:377px"><svg width="14" height="14" fill="#888"><path d="M2 1h3l1 3-2 1c1 2 3 4 5 5l1-2 3 1v3c0 1-1 2-2 2C5 14 0 9 0 3c0-1 1-2 2-2z"/></svg>Phone number</div>
  <div class="field" style="left:222px;top:3735px;width:768px;height:120px;align-items:flex-start;padding-top:22px"><svg width="14" height="13" fill="#888"><ellipse cx="7" cy="6" rx="7" ry="5"/><path d="M2 9l-1 4 4-2z"/></svg>Leave Message</div>
  <div class="btn" style="left:485px;top:3877px;width:245px;height:48px;font-size:15px">SEND MESSAGE</div>
</section>

<footer>
  <div class="logo" style="left:125px;top:4100px">
    <div class="logo-mark" style="width:46px;height:46px"></div>
    <div class="logo-text" style="font-size:32px">VERDELL<div style="font-size:17px;font-weight:400;color:var(--green);letter-spacing:5px;margin-top:4px">TREE CARE</div></div>
  </div>
  <p class="abs" style="left:128px;top:4198px;font-size:12px;line-height:22px;color:#555">Copyright © 2024 Verdell Tree Care<br>All Right Reserved</p>

  <div class="foot-col" style="left:425px"></div>
  <div class="foot-col" style="left:646px"></div>
  <div class="foot-col" style="left:925px"></div>

  <div class="foot-h" style="left:447px;top:4085px">NAVIGATION</div>
  <div class="foot-list" style="left:448px;top:4128px"><span style="text-decoration:underline">Home</span><br>About Us<br>Services<br>Blogs<br>Contact</div>

  <div class="foot-h" style="left:670px;top:4085px">CONTACT US</div>
  <svg class="abs" style="left:670px;top:4140px" width="28" height="28" fill="none" stroke="#888" stroke-width="1.5"><path d="M5 2h6l2 6-4 2c2 4 5 7 9 9l2-4 6 2v6c0 2-2 3-4 3C11 26 2 17 2 6c0-2 1-4 3-4z"/></svg>
  <div class="abs" style="left:712px;top:4138px;font-size:12px;line-height:17px;color:#555">Phone number<br><b style="color:var(--ink)">(555) 014-2290<br>(555) 017-4418</b></div>
  <svg class="abs" style="left:670px;top:4218px" width="28" height="22" fill="none" stroke="#888" stroke-width="1.5"><rect x="1" y="1" width="26" height="20"/><path d="M1 1l13 11 13-11"/></svg>
  <div class="abs" style="left:712px;top:4212px;font-size:12px;line-height:17px;color:#555">Email address<br><b style="color:var(--ink)">hello@verdelltreecare.example</b></div>

  <div class="foot-h" style="left:950px;top:4085px">FOLLOW US</div>
  <div class="social" style="left:944px" aria-label="Social profile"></div>
  <div class="social" style="left:981px" aria-label="Social profile"></div>
  <div class="social" style="left:1018px" aria-label="Social profile"></div>
  <div class="social" style="left:1060px" aria-label="Social profile"></div>
</footer>

</body>
</html>
```